Modern Business Card

Modern professional business card with more than just logo and demographic info. Something memorable.

We are a trendy/modern chiropractic group with an emphasis on neurology, hence the minimalist-type brain logo. We want to convey that modern and technical aspect with professionalism and the elite nature of our practice environment.

```html
<!DOCTYPE html>
<html lang="en">
<head>
<meta charset="utf-8">
<title>Nexa Chiropractic – Business Card</title>
<link rel="stylesheet" href="https://fonts.googleapis.com/css2?family=Cinzel:wght@500&family=Montserrat:wght@400;500&display=swap">
<style>
  :root {
    --backdrop: #a9a9a9;
    --card-black: #1c1c1d;
    --card-black-2: #262627;
    --paper-white: #ffffff;
    --brand-blue: #4a80c2;
    --text-white: #f2f2f2;
    --text-grey: #8c8c8c;
  }
  * { box-sizing: border-box; margin: 0; padding: 0; }
  html, body { width: 1200px; height: 930px; overflow: hidden; }
  body {
    background: var(--backdrop);
    font-family: "Montserrat", sans-serif;
    position: relative;
  }
  .card {
    position: absolute;
    left: 280px;
    width: 640px;
    height: 366px;
    border-radius: 22px;
    overflow: hidden;
    background: linear-gradient(135deg, var(--card-black-2), var(--card-black));
    box-shadow: 0 10px 24px rgba(0,0,0,.35);
  }
  .card--back { top: 70px; }
  .card--front { top: 494px; }

  .wordmark {
    font-family: "Cinzel", serif;
    font-weight: 500;
    color: var(--text-white);
    line-height: 1;
  }
  .wordmark__name { display: block; }

  .card--back .brand {
    position: absolute;
    left: 0; right: 0; top: 0; bottom: 0;
    display: flex;
    align-items: center;
    justify-content: center;
    gap: 22px;
  }
  .brand__dot {
    width: 58px; height: 58px;
    border-radius: 50%;
    background: var(--brand-blue);
  }
  .card--back .wordmark__name { font-size: 52px; letter-spacing: 2px; }
  .card--back .wordmark__sub { font-size: 27px; letter-spacing: 1px; margin-top: 4px; }

  .front-panel {
    position: absolute;
    right: 0; top: 0;
    width: 330px; height: 366px;
  }

  .front-info {
    position: absolute;
    left: 44px; top: 48px;
    color: var(--text-white);
  }
  .card--front .wordmark__name { font-size: 40px; letter-spacing: 1.5px; }
  .card--front .wordmark__sub { font-size: 21px; letter-spacing: .8px; margin-top: 3px; }

  .person { margin-top: 34px; margin-left: 48px; }
  .person__name {
    font-family: "Cinzel", serif;
    font-size: 19px;
    letter-spacing: 1px;
    color: var(--text-white);
  }
  .person__name .surname { color: var(--brand-blue); }
  .person__role { font-size: 14px; margin-top: 3px; }

  .address { margin: 18px 0 0 48px; font-size: 14px; line-height: 1.4; }

  .contacts { list-style: none; margin: 14px 0 0 24px; font-size: 14px; }
  .contacts li { display: flex; align-items: center; gap: 12px; line-height: 1.6; }
  .contacts svg { width: 13px; height: 13px; flex: none; }
  .contacts .accent { color: var(--brand-blue); }
</style>
</head>
<body>

  <section class="card card--back" aria-label="Card back">
    <div class="brand">
      <span class="brand__dot"></span>
      <div class="wordmark">
        <span class="wordmark__name">NEXA</span>
        <span class="wordmark__name wordmark__sub">CHIROPRACTIC</span>
      </div>
    </div>
  </section>

  <section class="card card--front" aria-label="Card front">
    <svg class="front-panel" viewBox="0 0 330 366" aria-hidden="true">
      <path d="M60 0 H330 V366 H20 C60 300 10 250 40 190 C70 130 20 80 60 0 Z" fill="var(--paper-white)"/>
      <circle cx="190" cy="180" r="92" fill="var(--brand-blue)"/>
    </svg>

    <div class="front-info">
      <div class="wordmark">
        <span class="wordmark__name">NEXA</span>
        <span class="wordmark__name wordmark__sub">CHIROPRACTIC</span>
      </div>

      <div class="person">
        <p class="person__name">MARK <span class="surname">ELLISON</span></p>
        <p class="person__role">Director</p>
      </div>

      <p class="address">1187 Cedar Ridge Lane<br>Salem, OR 97301</p>

      <ul class="contacts">
        <li>
          <svg viewBox="0 0 24 24"><path fill="var(--brand-blue)" d="M6.6 10.8a15 15 0 0 0 6.6 6.6l2.2-2.2a1 1 0 0 1 1-.25 11.4 11.4 0 0 0 3.6.57 1 1 0 0 1 1 1V20a1 1 0 0 1-1 1A17 17 0 0 1 3 4a1 1 0 0 1 1-1h3.5a1 1 0 0 1 1 1c0 1.25.2 2.45.57 3.6a1 1 0 0 1-.25 1z"/></svg>
          <span>(555) 218-4470</span>
        </li>
        <li>
          <svg viewBox="0 0 24 24"><rect x="2" y="5" width="20" height="14" rx="2" fill="none" stroke="var(--brand-blue)" stroke-width="2.4"/><path d="M2 6l10 7 10-7" fill="none" stroke="var(--brand-blue)" stroke-width="2.4"/></svg>
          <span>hello@nexachiro.com</span>
        </li>
        <li>
          <svg viewBox="0 0 24 24"><circle cx="12" cy="12" r="10" fill="none" stroke="var(--brand-blue)" stroke-width="2.2"/><path d="M2 12h20M12 2c3 3 3 17 0 20M12 2c-3 3-3 17 0 20" fill="none" stroke="var(--brand-blue)" stroke-width="2"/></svg>
          <span>www.<span class="accent">nexachiro</span>.com</span>
        </li>
      </ul>
    </div>
  </section>

</body>
</html>
```